RESINE DENTAIRE ROSE box for dental resine pink to repair dentures broken

I will need a design for a box of pink dental resin. It is a pink dental resin which is intended for sale to individuals on Brindleway to repair or make small touch-ups or modifications to their dental prostheses. The title RESINE DENTAIRE ROSE must be clearly visible as well as the company logo. .I leave it to your creative mind to make an attractive and highly impactful and clearly visible sales design.
It is also necessary to make it clear to buyers through text or a vector image the purpose of the product: to repair a dental prosthesis.
Faible participation designers
Particulars who have need to repair their dentures

```html
<!DOCTYPE html>
<html lang="fr">
<head>
<meta charset="utf-8">
<title>Résine Dentaire Rose – emballage</title>
<link rel="stylesheet" href="https://fonts.googleapis.com/css2?family=Libre+Baskerville:wght@700&family=Montserrat:wght@400;600&display=swap">
<style>
  :root{
    --paper:#f4f4f3;
    --bg:#ffffff;
    --salmon:#e8806a;
    --salmon-light:#f0a08e;
    --salmon-pale:#f6c2b4;
    --green:#6ba539;
    --ink:#1e1e1e;
    --hazard:#e4572e;
  }
  *{box-sizing:border-box;margin:0;padding:0}
  html,body{width:1200px;height:761px;overflow:hidden;background:var(--bg)}
  body{position:relative;font-family:"Montserrat",sans-serif;color:var(--ink)}

  .panel{position:absolute;background:var(--paper);overflow:hidden}
  .panel-top{left:390px;top:70px;width:560px;height:110px;border-bottom:1px solid #e2e2e2}
  .panel-side{left:250px;top:180px;width:140px;height:480px;border-right:1px solid #e2e2e2}
  .panel-front{left:390px;top:180px;width:560px;height:480px}

  .wave{position:absolute;inset:0;width:100%;height:100%}

  /* top panel */
  .maker-address{position:absolute;left:70px;top:16px;font-size:10.5px;line-height:13px;font-weight:400;letter-spacing:.3px;text-transform:uppercase}
  .safety-icons{position:absolute;left:70px;top:84px;display:flex;gap:8px;align-items:center}
  .safety-icons svg{display:block}

  /* front panel */
  .brand{position:absolute;right:34px;top:48px;display:flex;align-items:center;gap:10px}
  .brand-mark{width:30px;height:30px;background:var(--green);flex:none}
  .brand-name{font-family:"Montserrat",sans-serif;font-weight:600;color:var(--green);font-size:19px;line-height:21px;letter-spacing:1px;text-transform:uppercase}
  .brand-since{position:absolute;right:34px;top:104px;font-size:10px;font-weight:600;color:#3f7fb2;letter-spacing:.5px}

  .product-illustration{position:absolute;left:322px;top:170px;width:200px;height:140px;border-radius:40% 40% 48% 48%;background:radial-gradient(ellipse at 50% 35%,#ffffff 0%,#f7dbe0 35%,#ec9aa7 75%,#e68595 100%)}

  .product-title{position:absolute;left:96px;top:300px;font-family:"Libre Baskerville",serif;font-weight:700;color:var(--salmon);font-size:58px;line-height:60px;letter-spacing:.5px;text-transform:uppercase}

  .shade-options{position:absolute;left:100px;bottom:38px;display:flex;gap:22px;align-items:center;font-size:17px;letter-spacing:.3px}
  .shade{display:flex;align-items:center;gap:8px}
  .shade-box{width:26px;height:26px;border:2.5px solid var(--ink);position:relative}
  .shade-box svg{position:absolute;left:1px;top:-6px}

  /* side panel */
  .side-title{position:absolute;left:22px;top:30px;writing-mode:vertical-rl;font-family:"Libre Baskerville",serif;font-weight:700;color:var(--salmon);font-size:34px;line-height:38px;text-transform:uppercase}
  .side-brand{position:absolute;left:98px;bottom:50px;writing-mode:vertical-rl;display:flex;align-items:center;gap:6px;font-weight:600;color:var(--green);font-size:11px;letter-spacing:1px;text-transform:uppercase}
  .side-brand .brand-mark{width:14px;height:14px}
</style>
</head>
<body>

  <section class="panel panel-top" aria-label="Rabat supérieur">
    <svg class="wave" viewBox="0 0 560 110" preserveAspectRatio="none" aria-hidden="true">
      <path d="M0 0 H70 Q40 60 0 110 Z" fill="var(--salmon-light)"/>
    </svg>
    <p class="maker-address">Laboratoire Calidor<br>Valcourt 2 B<br>12 Rue des Tilleuls<br>04180 Valcourt Cedex 02<br>04 27 50 63 18</p>
    <div class="safety-icons" aria-label="Pictogrammes de sécurité">
      <svg width="18" height="16" viewBox="0 0 18 16"><path d="M9 1 L17 15 H1 Z" fill="none" stroke="var(--ink)" stroke-width="1.5"/><path d="M9 6 V10 M9 12 V13" stroke="var(--ink)" stroke-width="1.5"/></svg>
      <svg width="18" height="16" viewBox="0 0 18 16"><rect width="18" height="16" fill="var(--hazard)"/><path d="M5 4 L13 12 M13 4 L5 12" stroke="var(--ink)" stroke-width="2"/></svg>
      <svg width="18" height="16" viewBox="0 0 18 16"><rect width="18" height="16" fill="var(--hazard)"/><path d="M9 3 Q13 8 9 13 Q5 8 9 3Z" fill="var(--ink)"/></svg>
      <span style="font-size:14px;font-weight:600">CE</span>
      <svg width="18" height="16" viewBox="0 0 18 16"><path d="M4 2 H14 L9 8 L14 14 H4 L9 8 Z" fill="none" stroke="var(--ink)" stroke-width="1.5"/></svg>
    </div>
  </section>

  <section class="panel panel-side" aria-label="Côté de la boîte">
    <svg class="wave" viewBox="0 0 140 480" preserveAspectRatio="none" aria-hidden="true">
      <path d="M0 0 H140 V110 Q60 250 0 480 Z" fill="var(--salmon-pale)"/>
      <path d="M0 0 H70 Q20 200 0 480 Z" fill="var(--salmon-light)"/>
    </svg>
    <h2 class="side-title">Résine<br>Dentaire</h2>
    <div class="side-brand"><span class="brand-mark"></span>Laboratoire Calidor</div>
  </section>

  <section class="panel panel-front" aria-label="Face avant">
    <svg class="wave" viewBox="0 0 560 480" preserveAspectRatio="none" aria-hidden="true">
      <path d="M0 0 H150 Q170 90 110 220 Q40 360 30 480 H0 Z" fill="var(--salmon-light)"/>
      <path d="M0 0 H80 Q110 120 50 260 Q10 370 10 480 H0 Z" fill="var(--salmon-pale)" opacity=".7"/>
    </svg>

    <div class="brand"><span class="brand-mark"></span><span class="brand-name">Laboratoire<br>Calidor</span></div>
    <span class="brand-since">Depuis 1990</span>

    <div class="product-illustration" role="img" aria-label="Illustration d'une prothèse dentaire complète, gencive rose et dents blanches"></div>

    <h1 class="product-title">Résine<br>Dentaire</h1>

    <div class="shade-options">
      <span class="shade"><span class="shade-box"></span>BLANCHE</span>
      <span class="shade"><span class="shade-box"><svg width="26" height="30" viewBox="0 0 26 30"><path d="M3 16 L10 25 L24 2" fill="none" stroke="var(--ink)" stroke-width="4"/></svg></span>ROSE</span>
      <span class="shade"><span class="shade-box"></span>TRANSPERENTE</span>
    </div>
  </section>

</body>
</html>
```